Social Media Graphics - Oakline Push REVISED

Create 6-7 individual social media graphics (square size) to encourage folks to join our online course called:

The Harvest Ledger Circle
How to Launch a Multi-Million Business From Scratch
Sign Up Today!

IMPORTANT: Make the largest and most prominent text on the graphic be: How to Launch a Multi-Million Business From Scratch

For the color scheme of the graphics, let's try a blue color palette; make sure the graphics appeal to both men and women

Make sure each graphic contains 1 of the 3 pics attached (crop pic as needed); and make sure one of the graphics is all TEXT only.

Target Market(s)

men and women looking to start a business

Industry/Entity Type

Entrepreneurship

Colors
0054AA
0677BA
7BADD7
CADEEF
E8F1F8

Requirements
Must have
• All the text and use the 3 pics provided; one graphic can be all text; Simple, modern design that's easy to read

```html
<!DOCTYPE html>
<html lang="en">
<head>
<meta charset="UTF-8">
<title>The Harvest Ledger Circle – Social Graphic</title>
<link href="https://fonts.googleapis.com/css2?family=Oswald:wght@600;700&display=swap" rel="stylesheet">
<style>
  :root {
    --navy: #10325a;
    --royal: #0b58a8;
    --royal-deep: #084a92;
    --rule: #1c78c4;
    --sky: #7cbcf6;
    --yellow: #fff200;
    --white: #ffffff;
    --button-text: #e8f1f8;
  }
  * { margin: 0; padding: 0; box-sizing: border-box; }
  html, body { width: 1200px; height: 1200px; overflow: hidden; background: var(--royal); }
  .graphic {
    position: relative;
    width: 1200px;
    height: 1200px;
    background: linear-gradient(180deg, var(--royal) 0%, var(--royal-deep) 100%);
    font-family: "Oswald", "Arial Narrow", sans-serif;
    font-weight: 700;
    text-transform: uppercase;
    overflow: hidden;
  }
  .title-bar {
    position: absolute; left: 0; top: 0; width: 1200px; height: 114px;
    background: var(--navy);
    display: flex; align-items: center; justify-content: center;
    font-size: 62px; letter-spacing: 0.5px; line-height: 1;
    white-space: nowrap;
  }
  .title-bar .accent { color: var(--yellow); }
  .title-bar .cool { color: var(--sky); margin-left: 16px; }
  .rule { position: absolute; left: 0; width: 1200px; height: 8px; background: var(--rule); }
  .rule--top { top: 114px; }
  .rule--bottom { top: 609px; }
  .hero-photo {
    position: absolute; left: 0; top: 122px; width: 1200px; height: 487px;
    background:
      radial-gradient(ellipse 30% 45% at 25% 55%, rgba(170,200,230,0.35), transparent 70%),
      radial-gradient(ellipse 28% 50% at 78% 62%, rgba(150,190,230,0.3), transparent 70%),
      linear-gradient(180deg, #0a4f9c 0%, #1466b8 100%);
  }
  .headline-band {
    position: absolute; left: 0; top: 617px; width: 1200px; height: 377px;
    background: var(--navy);
    display: flex; align-items: center; justify-content: center;
    text-align: center;
  }
  .headline {
    font-size: 96px; line-height: 106px; letter-spacing: 1px;
    font-weight: 700; white-space: nowrap;
  }
  .headline span { display: block; }
  .headline .line-white { color: var(--white); }
  .headline .line-yellow { color: var(--yellow); }
  .headline .line-sky { color: var(--sky); }
  .cta {
    position: absolute; left: 367px; top: 1042px; width: 464px; height: 111px;
    background: var(--navy);
    border-radius: 18px;
    border-top: 4px solid var(--rule);
    display: flex; align-items: center; justify-content: center;
    color: var(--button-text);
    font-size: 50px; font-weight: 600; letter-spacing: 0.5px;
    white-space: nowrap;
  }
</style>
</head>
<body>
  <main class="graphic">
    <header class="title-bar">
      <span class="accent">The Harvest Ledger</span><span class="cool">Circle</span>
    </header>
    <div class="rule rule--top"></div>
    <div class="hero-photo" role="img" aria-label="Photo of stacked dollar bills beside a pocket watch in sand, tinted blue"></div>
    <div class="rule rule--bottom"></div>
    <section class="headline-band">
      <h1 class="headline">
        <span class="line-white">How to Launch a</span>
        <span class="line-yellow">Multi-Million Business</span>
        <span class="line-sky">From Scratch</span>
      </h1>
    </section>
    <div class="cta">Sign Up Today!</div>
  </main>
</body>
</html>
```